DuePath.com website design

We are a collection agency that collects debt from past residents of apartments on behalf of Property Management Companies. We are want to design a 3 page website with - Home - How it Works - Schedule Demo. We'd like a sketch of a skyline showing high rise apartment buildings, houses, shops, etc. We would like for there to be some animation, possibly clouds and the sun slowly moving. Maybe kids playing ball or catch or something like that. Bird flying and landing. An electric car charging (to indicate we are modern). We are looking for a friendly community vibe. The site will also need a button "Property Managers Login". When some comes to the site we would like a pop up that says "Property Managers Click Here/Past Residents Click Here" with a different icon for each that relates to the description. I've included a link to a test site we had designed so feel free to use some of the copy from it. We just aren't happy with the design. On the Home page our tag line should be "Get more payments, faster, from past residents!" and "Digital First, NOT Digital Only". All without transaction fees, we don't get paid unless we get you paid first!
Additional selling points:

24 hour virtual agent and virtual telephone agent so we don't miss any opportunities to GET YOUR MONEY!

Old school collection strategies meet cutting edge technology to create effective work flow algorithms to put the best debt collectors on your accounts with data driven intelligence to determine the best way to get paid.

No Subscription Fees
No Payment Processing Fees
No Software Fees
No Mail, Email or TXT Fees

Inquire about our FIRST PARTY accounts receivable outsourcing. You may qualify for free post move out A/R processing and AI payment negotiator for the low hanging fruit. Don't pay full collection commission when there wasn't a full collection attempt!

For the How it Works page - See the page from our previous design. I will include the link below. Please come up with your own version of this but you can use the copy from this page.

The schedule demo page will be a form that will feed to our CRM that will include:
Name
Email
Company
Title
Phone Number
Number of Units
Tell us how we can help you: (a box for them provide details)

Also include our phone number at the bottom with something like

Here is a link to our previous design test site:
https://brookpreview.net/duepath-new/
I've attached an image of the back end so you can get an idea of the colors we need, I've also included our logo. For the most part we would like most of the site to match the blue colors from our logo, but we do need to incorporate some of the yellow in the images I've attached. Possibly make the buttons on the site the yellow color? Make the sun Match the yellow? I'll leave it up to you.

```html
<!DOCTYPE html>
<html lang="en">
<head>
<meta charset="utf-8">
<title>DuePath – Home page screens</title>
<link href="https://fonts.googleapis.com/css2?family=Fjalla+One&family=Montserrat:wght@400;500;600;700&display=swap" rel="stylesheet">
<style>
:root{
  --navy:#0d3d73;
  --cyan:#1fb5d0;
  --ink:#2a2f36;
  --muted:#6b7580;
  --ghost:#e9ecef;
  --field:#fafbfc;
  --line:#cfd5db;
  --foot:#eef8fb;
  --stage:#b3b3b3;
  --dim:rgba(22,32,44,.62);
}
*{box-sizing:border-box;margin:0;padding:0}
html,body{width:1152px;height:1200px;overflow:hidden;background:var(--stage);font-family:"Montserrat",sans-serif;color:var(--ink)}
.screen{position:absolute;top:65px;width:831px;height:1747px;transform:scale(.6125);transform-origin:0 0;background:#fff;overflow:hidden}
.screen--popup{left:52px}
.screen--plain{left:591px}
.abs{position:absolute}
.brand{font-family:"Fjalla One",sans-serif;color:var(--navy);display:flex;align-items:center;gap:10px}
.brand__mark{width:40px;height:40px;border-radius:50%;background:var(--cyan)}
.brand__name{font-size:38px;line-height:1}
.nav{top:22px;left:425px;display:flex;gap:27px;font-size:12px;font-weight:700;color:var(--navy);align-items:center}
.pill{position:absolute;border-radius:20px;font-size:11.5px;font-weight:600;color:#fff;display:flex;align-items:center;justify-content:center;letter-spacing:.2px}
.pill--navy{background:var(--navy)}
.pill--cyan{background:var(--cyan)}
.pill--outline{background:#fff;border:1.5px solid var(--cyan);color:var(--cyan)}
.headline{font-family:"Fjalla One",sans-serif;color:var(--navy);text-align:center;width:831px;left:0}
.headline em{font-style:normal;color:var(--cyan)}
.ghost{font-family:"Fjalla One",sans-serif;color:var(--ghost);font-size:72px;text-align:center;width:831px;left:0}
.skyline{position:absolute;background:linear-gradient(180deg,#fff 0%,#e4f1f6 35%,#f3b25b 70%,#e2563c 100%)}
.skyline--faint{background:linear-gradient(180deg,rgba(255,255,255,0) 0%,#edf4f2 50%,#f4ecd6 100%)}
.dots span{display:block;width:6px;height:6px;border-radius:50%;background:#9aa3ab;margin-bottom:8px}
.dots span.on{background:var(--cyan)}
.features{top:400px;left:100px;width:632px;height:127px;display:flex}
.feature{flex:1;display:flex;flex-direction:column;align-items:center;justify-content:flex-end;padding-bottom:22px;color:#fff;font-size:12px;font-weight:700;text-align:center;line-height:1.15}
.feature svg{margin-bottom:16px}
.feature:nth-child(odd){background:var(--navy)}
.feature:nth-child(even){background:var(--cyan)}
.ring{left:291px;top:681px;width:218px;height:218px;border-radius:50%;border:3px solid var(--cyan)}
.core{left:313px;top:703px;width:174px;height:174px;border-radius:50%;background:#fff;box-shadow:0 6px 22px rgba(0,0,0,.12);display:flex;align-items:center;justify-content:center;font-family:"Fjalla One",sans-serif;font-size:34px;color:var(--navy)}
.node{width:9px;height:9px;border-radius:50%;background:#fff;border:2px solid var(--navy)}
.step{font-size:12px;line-height:18px;color:var(--ink)}
.step--r{text-align:right}
.badge{width:52px;height:52px;border-radius:50%;display:flex;align-items:center;justify-content:center}
.badge--cyan{background:var(--cyan)}
.badge--navy{background:var(--navy)}
.banner{top:1048px;left:0;width:831px;height:126px;background:var(--navy)}
.banner__kicker{font-family:"Fjalla One",sans-serif;color:var(--cyan);font-size:14px;line-height:19px;left:117px;top:26px}
.banner__title{font-family:"Fjalla One",sans-serif;color:#fff;font-size:33px;left:117px;top:64px}
.field{position:absolute;height:39px;border:1px solid var(--line);background:var(--field);font-size:9px;color:var(--muted);padding:14px 0 0 18px}
.footer{top:1629px;left:0;width:831px;height:118px;background:var(--foot);border-top:4px solid var(--cyan)}
.footer__links{left:101px;top:35px;font-size:12.5px;font-weight:700;color:var(--navy);display:flex;gap:14px}
.footer__copy{left:101px;top:70px;font-size:9.5px;color:var(--ink)}
.social{display:flex;gap:10px;left:528px;top:76px}
.social span{width:19px;height:19px;border-radius:50%;background:var(--navy)}
.shade{left:0;top:0;width:831px;height:1747px;background:var(--dim)}
.modal{left:139px;top:202px;width:553px;height:345px;background:#fff;border-radius:18px;overflow:hidden}
.modal__close{left:650px;top:199px;width:42px;height:42px;border-radius:50%;background:var(--navy);display:flex;align-items:center;justify-content:center}
.choice{position:absolute;left:106px;width:342px;height:39px;border-radius:20px;color:#fff;font-size:12.5px;font-weight:700;display:flex;align-items:center;padding-left:50px}
.choice__icon{position:absolute;left:3px;top:3px;width:33px;height:33px;border-radius:50%;background:#fff;display:flex;align-items:center;justify-content:center}
</style>
</head>
<body>

<!-- Screen with entry popup -->
<section class="screen screen--popup">
  <header>
    <div class="brand abs" style="left:100px;top:12px"><span class="brand__mark"></span><span class="brand__name">DuePath</span></div>
    <nav class="nav abs"><span>HOME</span><span>HOW IT WORKS</span></nav>
    <a class="pill pill--cyan" style="left:608px;top:16px;width:122px;height:30px">SCHEDULE DEMO</a>
  </header>
  <h1 class="headline abs" style="top:106px;font-size:31px">Digital First, NOT <em>Digital Only</em></h1>
  <a class="pill pill--navy" style="left:355px;top:158px;width:122px;height:28px">SCHEDULE DEMO</a>
  <div class="skyline" style="left:0;top:180px;width:831px;height:210px" role="img" aria-label="Illustrated city skyline with apartment towers, houses, shops, a plane and a drone"></div>
  <div class="dots abs" style="left:794px;top:205px"><span></span><span class="on"></span><span></span></div>
  <div class="abs" style="left:0;top:390px;width:831px;height:10px;background:var(--cyan)"></div>
  <div class="features abs">
    <div class="feature"><svg width="44" height="44" viewBox="0 0 44 44" fill="none" stroke="#fff" stroke-width="2.5"><circle cx="22" cy="22" r="18"/><path d="M27 15h-7a4 4 0 0 0 0 8h4a4 4 0 0 1 0 8h-8M22 11v4M22 31v4"/></svg>NO SUBSCRIPTION<br>FEES</div>
    <div class="feature"><svg width="44" height="44" viewBox="0 0 44 44" fill="none" stroke="#fff" stroke-width="2.5"><circle cx="22" cy="22" r="18"/><path d="M9 35 35 9"/></svg>NO PAYMENT<br>PROCESSING FEES</div>
    <div class="feature"><svg width="48" height="44" viewBox="0 0 48 44" fill="none" stroke="#fff" stroke-width="2.5"><rect x="4" y="8" width="40" height="26" rx="2"/><path d="M18 40h12M24 34v6"/></svg>NO SOFTWARE<br>FEES</div>
    <div class="feature"><svg width="48" height="44" viewBox="0 0 48 44" fill="none" stroke="#fff" stroke-width="2.5"><rect x="4" y="10" width="40" height="28" rx="2"/><path d="m4 12 20 14 20-14"/></svg>NO MAIL, EMAIL<br>OR TXT FEES</div>
  </div>

  <div class="ghost abs" style="top:548px">How it Works</div>
  <h2 class="headline abs" style="top:572px;font-size:34px">How it <em>Works</em></h2>
  <div class="ring abs"></div>
  <div class="core abs">DuePath</div>
  <span class="node abs" style="left:315px;top:712px"></span><span class="node abs" style="left:477px;top:712px"></span>
  <span class="node abs" style="left:285px;top:783px"></span><span class="node abs" style="left:505px;top:783px"></span>
  <span class="node abs" style="left:314px;top:859px"></span><span class="node abs" style="left:476px;top:859px"></span>
  <div class="badge badge--cyan abs" style="left:254px;top:669px"><svg width="24" height="24" viewBox="0 0 24 24" fill="none" stroke="#fff" stroke-width="2"><rect x="6" y="2" width="12" height="20" rx="2"/><path d="M10 18h4"/></svg></div>
  <div class="badge badge--cyan abs" style="left:494px;top:669px"><svg width="24" height="24" viewBox="0 0 24 24" fill="none" stroke="#fff" stroke-width="2"><rect x="2" y="5" width="20" height="14" rx="1"/><path d="m2 6 10 7 10-7"/></svg></div>
  <div class="badge badge--navy abs" style="left:209px;top:766px"><svg width="24" height="24" viewBox="0 0 24 24" fill="none" stroke="#fff" stroke-width="2"><path d="M4 8h14l-4-4M20 16H6l4 4"/></svg></div>
  <div class="badge badge--cyan abs" style="left:524px;top:766px"><svg width="24" height="24" viewBox="0 0 24 24" fill="none" stroke="#fff" stroke-width="2"><circle cx="12" cy="12" r="9"/><path d="M3 12h18M12 3c4 4 4 14 0 18M12 3c-4 4-4 14 0 18"/></svg></div>
  <div class="badge badge--cyan abs" style="left:258px;top:862px"><svg width="24" height="24" viewBox="0 0 24 24" fill="none" stroke="#fff" stroke-width="2"><rect x="4" y="3" width="16" height="18" rx="1"/><path d="m7 16 4-4 3 3 4-5"/></svg></div>
  <div class="badge badge--navy abs" style="left:494px;top:862px"><svg width="24" height="24" viewBox="0 0 24 24" fill="none" stroke="#fff" stroke-width="2"><path d="M20 12a8 8 0 1 1-3-6.2M20 4v5h-5"/></svg></div>
  <p class="step step--r abs" style="left:80px;top:677px;width:166px">We offer convenient<br>payment platforms</p>
  <p class="step abs" style="left:553px;top:677px">We contact your past resident<br>before they are delinquent</p>
  <p class="step step--r abs" style="left:60px;top:772px;width:144px">Transfer accounts<br>to DuePath</p>
  <p class="step abs" style="left:582px;top:772px">Intense collections begins<br>once delinquent</p>
  <p class="step step--r abs" style="left:60px;top:872px;width:191px">Credit reporting and legal<br>action when possible</p>
  <p class="step abs" style="left:556px;top:862px">Continued collection attempts<br>throughout the lifecycle of<br>the account</p>
  <div class="skyline skyline--faint" style="left:0;top:960px;width:831px;height:88px" role="img" aria-label="Faint pastel city skyline"></div>
  <a class="pill pill--navy" style="left:291px;top:958px;width:122px;height:29px">SCHEDULE DEMO</a>
  <a class="pill pill--outline" style="left:418px;top:958px;width:122px;height:29px">CONTACT US</a>

  <section class="banner abs">
    <p class="banner__kicker abs">LET DUEPATH EARN YOUR BUSINESS, IF WE DON'T GET YOU<br>PAID WE DON'T CHARGE YOU ANYTHING</p>
    <h2 class="banner__title abs">We Want To Earn Your Business</h2>
    <a class="pill pill--cyan" style="left:592px;top:31px;width:122px;height:28px">SCHEDULE DEMO</a>
  </section>

  <div class="ghost abs" style="top:1198px">Schedule A Demo</div>
  <h2 class="headline abs" style="top:1222px;font-size:34px">Schedule <em>A Demo</em></h2>
  <form>
    <div class="field" style="left:101px;top:1302px;width:310px">Name</div>
    <div class="field" style="left:419px;top:1302px;width:311px">Email</div>
    <div class="field" style="left:101px;top:1350px;width:310px">Company</div>
    <div class="field" style="left:419px;top:1350px;width:311px">Title</div>
    <div class="field" style="left:101px;top:1397px;width:310px">Phone Number</div>
    <div class="field" style="left:419px;top:1397px;width:311px">Number of Units</div>
    <div class="field" style="left:101px;top:1445px;width:629px;height:72px">Tell us how we can help you:</div>
  </form>
  <div class="skyline skyline--faint" style="left:0;top:1540px;width:831px;height:85px" role="img" aria-label="Faint pastel city skyline"></div>
  <a class="pill pill--cyan" style="left:343px;top:1538px;width:145px;height:28px">SUBMIT MESSAGE</a>
  <footer class="footer abs">
    <nav class="footer__links abs"><span>HOME</span><span>/</span><span>HOW IT WORKS</span><span>/</span><span>ABOUT US</span><span>/</span><span>CONTACT</span></nav>
    <p class="footer__copy abs">©Copyright 2022 Duepath. All Right Reserved</p>
    <div class="brand abs" style="left:535px;top:22px"><span class="brand__mark" style="width:34px;height:34px"></span><span class="brand__name" style="font-size:32px">DuePath</span></div>
    <div class="social abs"><span></span><span></span><span></span><span></span></div>
  </footer>

  <div class="shade abs"></div>
  <div class="modal abs">
    <div class="brand abs" style="left:130px;top:56px"><span class="brand__mark" style="width:60px;height:60px"></span><span class="brand__name" style="font-size:52px">DuePath</span></div>
    <a class="choice" style="top:159px;background:var(--navy)"><span class="choice__icon"><svg width="20" height="20" viewBox="0 0 24 24" fill="none" stroke="#0d3d73" stroke-width="2"><rect x="4" y="3" width="16" height="18"/><path d="M8 7h2M14 7h2M8 11h2M14 11h2M10 21v-5h4v5"/></svg></span>PROPERTY MANAGERS CLICK HERE</a>
    <a class="choice" style="top:214px;background:var(--cyan)"><span class="choice__icon"><svg width="20" height="20" viewBox="0 0 24 24" fill="none" stroke="#0d3d73" stroke-width="2"><path d="M3 11 12 4l9 7M5 10v10h14V10M10 20v-6h4v6"/></svg></span>PAST RESIDENTS CLICK HERE</a>
    <div class="skyline skyline--faint" style="left:0;top:255px;width:553px;height:90px" role="img" aria-label="Faint pastel city skyline"></div>
  </div>
  <div class="modal__close abs"><svg width="16" height="16" viewBox="0 0 16 16" stroke="#fff" stroke-width="3"><path d="M2 2l12 12M14 2 2 14"/></svg></div>
</section>

<!-- Screen without popup -->
<section class="screen screen--plain">
  <header>
    <div class="brand abs" style="left:100px;top:12px"><span class="brand__mark"></span><span class="brand__name">DuePath</span></div>
    <nav class="nav abs"><span>HOME</span><span>HOW IT WORKS</span></nav>
    <a class="pill pill--cyan" style="left:608px;top:16px;width:122px;height:30px">SCHEDULE DEMO</a>
  </header>
  <h1 class="headline abs" style="top:106px;font-size:31px">Digital First, NOT <em>Digital Only</em></h1>
  <div class="skyline" style="left:0;top:180px;width:831px;height:210px" role="img" aria-label="Illustrated city skyline with apartment towers, houses, shops, a plane and a drone"></div>
  <a class="pill pill--navy" style="left:355px;top:158px;width:122px;height:28px">SCHEDULE DEMO</a>
  <div class="dots abs" style="left:794px;top:205px"><span></span><span class="on"></span><span></span></div>
  <div class="abs" style="left:0;top:390px;width:831px;height:10px;background:var(--cyan)"></div>
  <div class="features abs">
    <div class="feature"><svg width="44" height="44" viewBox="0 0 44 44" fill="none" stroke="#fff" stroke-width="2.5"><circle cx="22" cy="22" r="18"/><path d="M27 15h-7a4 4 0 0 0 0 8h4a4 4 0 0 1 0 8h-8M22 11v4M22 31v4"/></svg>NO SUBSCRIPTION<br>FEES</div>
    <div class="feature"><svg width="44" height="44" viewBox="0 0 44 44" fill="none" stroke="#fff" stroke-width="2.5"><circle cx="22" cy="22" r="18"/><path d="M9 35 35 9"/></svg>NO PAYMENT<br>PROCESSING FEES</div>
    <div class="feature"><svg width="48" height="44" viewBox="0 0 48 44" fill="none" stroke="#fff" stroke-width="2.5"><rect x="4" y="8" width="40" height="26" rx="2"/><path d="M18 40h12M24 34v6"/></svg>NO SOFTWARE<br>FEES</div>
    <div class="feature"><svg width="48" height="44" viewBox="0 0 48 44" fill="none" stroke="#fff" stroke-width="2.5"><rect x="4" y="10" width="40" height="28" rx="2"/><path d="m4 12 20 14 20-14"/></svg>NO MAIL, EMAIL<br>OR TXT FEES</div>
  </div>

  <div class="ghost abs" style="top:548px">How it Works</div>
  <h2 class="headline abs" style="top:572px;font-size:34px">How it <em>Works</em></h2>
  <div class="ring abs"></div>
  <div class="core abs">DuePath</div>
  <span class="node abs" style="left:315px;top:712px"></span><span class="node abs" style="left:477px;top:712px"></span>
  <span class="node abs" style="left:285px;top:783px"></span><span class="node abs" style="left:505px;top:783px"></span>
  <span class="node abs" style="left:314px;top:859px"></span><span class="node abs" style="left:476px;top:859px"></span>
  <div class="badge badge--cyan abs" style="left:254px;top:669px"><svg width="24" height="24" viewBox="0 0 24 24" fill="none" stroke="#fff" stroke-width="2"><rect x="6" y="2" width="12" height="20" rx="2"/><path d="M10 18h4"/></svg></div>
  <div class="badge badge--cyan abs" style="left:494px;top:669px"><svg width="24" height="24" viewBox="0 0 24 24" fill="none" stroke="#fff" stroke-width="2"><rect x="2" y="5" width="20" height="14" rx="1"/><path d="m2 6 10 7 10-7"/></svg></div>
  <div class="badge badge--navy abs" style="left:209px;top:766px"><svg width="24" height="24" viewBox="0 0 24 24" fill="none" stroke="#fff" stroke-width="2"><path d="M4 8h14l-4-4M20 16H6l4 4"/></svg></div>
  <div class="badge badge--cyan abs" style="left:524px;top:766px"><svg width="24" height="24" viewBox="0 0 24 24" fill="none" stroke="#fff" stroke-width="2"><circle cx="12" cy="12" r="9"/><path d="M3 12h18M12 3c4 4 4 14 0 18M12 3c-4 4-4 14 0 18"/></svg></div>
  <div class="badge badge--cyan abs" style="left:258px;top:862px"><svg width="24" height="24" viewBox="0 0 24 24" fill="none" stroke="#fff" stroke-width="2"><rect x="4" y="3" width="16" height="18" rx="1"/><path d="m7 16 4-4 3 3 4-5"/></svg></div>
  <div class="badge badge--navy abs" style="left:494px;top:862px"><svg width="24" height="24" viewBox="0 0 24 24" fill="none" stroke="#fff" stroke-width="2"><path d="M20 12a8 8 0 1 1-3-6.2M20 4v5h-5"/></svg></div>
  <p class="step step--r abs" style="left:80px;top:677px;width:166px">We offer convenient<br>payment platforms</p>
  <p class="step abs" style="left:553px;top:677px">We contact your past resident<br>before they are delinquent</p>
  <p class="step step--r abs" style="left:60px;top:772px;width:144px">Transfer accounts<br>to DuePath</p>
  <p class="step abs" style="left:582px;top:772px">Intense collections begins<br>once delinquent</p>
  <p class="step step--r abs" style="left:60px;top:872px;width:191px">Credit reporting and legal<br>action when possible</p>
  <p class="step abs" style="left:556px;top:862px">Continued collection attempts<br>throughout the lifecycle of<br>the account</p>
  <div class="skyline skyline--faint" style="left:0;top:960px;width:831px;height:88px" role="img" aria-label="Faint pastel city skyline"></div>
  <a class="pill pill--navy" style="left:291px;top:958px;width:122px;height:29px">SCHEDULE DEMO</a>
  <a class="pill pill--outline" style="left:418px;top:958px;width:122px;height:29px">CONTACT US</a>

  <section class="banner abs">
    <p class="banner__kicker abs">LET DUEPATH EARN YOUR BUSINESS, IF WE DON'T GET YOU<br>PAID WE DON'T CHARGE YOU ANYTHING</p>
    <h2 class="banner__title abs">We Want To Earn Your Business</h2>
    <a class="pill pill--cyan" style="left:592px;top:31px;width:122px;height:28px">SCHEDULE DEMO</a>
  </section>

  <div class="ghost abs" style="top:1198px">Schedule A Demo</div>
  <h2 class="headline abs" style="top:1222px;font-size:34px">Schedule <em>A Demo</em></h2>
  <form>
    <div class="field" style="left:101px;top:1302px;width:310px">Name</div>
    <div class="field" style="left:419px;top:1302px;width:311px">Email</div>
    <div class="field" style="left:101px;top:1350px;width:310px">Company</div>
    <div class="field" style="left:419px;top:1350px;width:311px">Title</div>
    <div class="field" style="left:101px;top:1397px;width:310px">Phone Number</div>
    <div class="field" style="left:419px;top:1397px;width:311px">Number of Units</div>
    <div class="field" style="left:101px;top:1445px;width:629px;height:72px">Tell us how we can help you:</div>
  </form>
  <div class="skyline skyline--faint" style="left:0;top:1540px;width:831px;height:85px" role="img" aria-label="Faint pastel city skyline"></div>
  <a class="pill pill--cyan" style="left:343px;top:1538px;width:145px;height:28px">SUBMIT MESSAGE</a>
  <footer class="footer abs">
    <nav class="footer__links abs"><span>HOME</span><span>/</span><span>HOW IT WORKS</span><span>/</span><span>ABOUT US</span><span>/</span><span>CONTACT</span></nav>
    <p class="footer__copy abs">©Copyright 2022 Duepath. All Right Reserved</p>
    <div class="brand abs" style="left:535px;top:22px"><span class="brand__mark" style="width:34px;height:34px"></span><span class="brand__name" style="font-size:32px">DuePath</span></div>
    <div class="social abs"><span></span><span></span><span></span><span></span></div>
  </footer>
</section>

</body>
</html>
```